Help design website for "Brightwater Civic Advisors" to advance the common good

Here is the Google doc link that lays out the design:

https://files.plumrivet.example/sheet/d/7QmTzR2wLx9KpVbN4hJcY8sEaUoFdG3iXkMnPq5rWt6/edit?usp=sharing

Here is the Google drive folder with the logos and photos: https://vault.plumrivet.example/open?id=4HkWp9LzQe2TxRvN8mBaYc3DsUoJfG6

The testimonials are being gathered and will be shared by Friday, 1/4.

The winner will also have to migrate the coding files to my hosting site.

Thank you for your help! Looking forward to seeing your designs.

Target Market(s)

Prospective clients

Industry/Entity Type

Non Profit

Coding

Coded - Design and coding required

Number of Pages Required

5+ page

Requirements
Must have
• Noted in the Google doc regarding layout.
Nice to have

```html
<!DOCTYPE html>
<html lang="en">
<head>
<meta charset="utf-8">
<title>Brightwater Civic Advisors — Services &amp; Testimonials</title>
<link href="https://fonts.googleapis.com/css2?family=Poppins:wght@500;600;700&family=PT+Sans:wght@400;700&display=swap" rel="stylesheet">
<style>
  :root {
    --brand-blue: #3d8bcf;
    --ink: #2a2a2a;
    --body-text: #3a3a3a;
    --footer-dark: #25252d;
    --pattern-band: #f3f4f6;
    --white: #ffffff;
  }
  * { box-sizing: border-box; margin: 0; padding: 0; }
  html, body { width: 760px; height: 1200px; overflow: hidden; background: var(--white); }
  body { position: relative; font-family: "PT Sans", Arial, sans-serif; color: var(--body-text); }

  .site-header { position: absolute; top: 0; left: 0; width: 760px; height: 78px; background: var(--brand-blue); }
  .brand { position: absolute; display: flex; align-items: center; gap: 10px; }
  .brand-mark { width: 14px; height: 14px; background: var(--white); flex: none; }
  .brand-name { font-family: "Poppins", Arial, sans-serif; font-weight: 500; color: var(--white); text-transform: uppercase; letter-spacing: 0.22em; line-height: 1.12; }
  .site-header .brand { left: 90px; top: 13px; }
  .site-header .brand-name { font-size: 13.5px; }
  .cta-button { position: absolute; left: 466px; top: 13px; width: 203px; height: 26px; border: 2px solid var(--white); color: var(--white); font-family: "Poppins", Arial, sans-serif; font-weight: 600; font-size: 8.6px; display: flex; align-items: center; justify-content: center; text-decoration: none; text-transform: uppercase; }
  .main-nav { position: absolute; right: 92px; top: 55px; display: flex; gap: 20px; }
  .main-nav a { color: var(--white); font-family: "Poppins", Arial, sans-serif; font-weight: 600; font-size: 8.4px; text-decoration: none; text-transform: uppercase; padding-bottom: 2px; }
  .main-nav a.is-active { border-bottom: 1px solid var(--white); }

  .hero-photo { position: absolute; top: 78px; left: 0; width: 760px; height: 352px;
    background: radial-gradient(ellipse at 60% 35%, #8a6e55 0%, #4a3a2e 40%, #1c1612 80%); }
  .hero-edge { position: absolute; top: 350px; left: 0; }

  .intro { position: absolute; top: 414px; left: 120px; width: 520px; text-align: center; }
  .intro h1 { font-family: "Poppins", Arial, sans-serif; font-weight: 700; font-size: 16.5px; color: var(--ink); margin-bottom: 14px; }
  .intro p { font-size: 10px; line-height: 1.3; }

  .card { position: absolute; background: var(--white); box-shadow: 0 2px 10px rgba(0,0,0,0.12); }
  .card-photo { position: absolute; left: 0; width: 100%; }
  .card-caption { position: absolute; left: 15px; right: 15px; bottom: 9px; color: var(--white); font-family: "Poppins", Arial, sans-serif; font-weight: 700; font-size: 9.4px; line-height: 1.25; text-transform: uppercase; }
  .card--left { left: 90px; top: 570px; width: 277px; height: 377px; }
  .card--left .card-photo { top: 0; height: 187px; background: linear-gradient(180deg, #7d9bb8 0%, #5d6e7a 35%, #3e4a3c 75%, #2c3a24 100%); }
  .card--right { left: 391px; top: 530px; width: 278px; height: 417px; }
  .card--right .card-photo { top: 0; height: 227px; background: linear-gradient(180deg, #6b5a48 0%, #3a3530 45%, #242226 100%); }
  .quote { position: absolute; left: 32px; top: 205px; width: 230px; font-size: 9px; line-height: 1.25; }
  .quote-mark { font-family: Georgia, serif; font-weight: 700; font-size: 24px; color: var(--ink); position: absolute; line-height: 1; }
  .quote-mark.open { left: 18px; top: 197px; }
  .quote-mark.close { left: 199px; top: 289px; }
  .attribution { position: absolute; font-size: 9px; line-height: 1.25; }
  .attribution strong { color: var(--ink); }
  .card--left .attribution { left: 32px; top: 339px; }
  .card--right .attribution { left: 33px; top: 376px; width: 235px; }

  .pattern-band { position: absolute; top: 952px; left: 0; width: 760px; height: 120px; background: var(--pattern-band); }
  .site-footer { position: absolute; top: 995px; left: 0; }
  .footer-content { position: absolute; top: 1060px; left: 0; width: 760px; height: 140px; }
  .footer-content .brand { left: 90px; top: 24px; gap: 14px; }
  .footer-content .brand-mark { width: 20px; height: 20px; background: var(--brand-blue); }
  .footer-content .brand-name { font-size: 19px; }
  .footer-divider { position: absolute; left: 388px; top: 16px; width: 1px; height: 90px; background: #4a4a55; }
  .footer-menu-title { position: absolute; left: 425px; top: 28px; color: var(--white); font-family: "Poppins", Arial, sans-serif; font-weight: 700; font-size: 7.4px; }
  .footer-links { position: absolute; left: 425px; top: 50px; display: flex; font-size: 7.6px; color: var(--white); }
  .footer-links a { color: var(--white); text-decoration: none; text-transform: uppercase; }
  .footer-links span { margin: 0 7px; }
  .copyright { position: absolute; left: 426px; top: 88px; color: var(--white); font-size: 7.4px; }
</style>
</head>
<body>
  <header class="site-header">
    <div class="brand"><span class="brand-mark"></span><span class="brand-name">Brightwater<br>Civic<br>Advisors</span></div>
    <a class="cta-button" href="#">Book a complimentary consultation</a>
    <nav class="main-nav">
      <a href="#">About</a>
      <a href="#" class="is-active">Services &amp; Testimonials</a>
      <a href="#">Media &amp; Impact</a>
      <a href="#">Contact</a>
    </nav>
  </header>

  <div class="hero-photo" role="img" aria-label="Mara speaking at a wooden podium with microphones on a dim stage"></div>
  <svg class="hero-edge" width="760" height="80" viewBox="0 0 760 80" aria-hidden="true">
    <polygon points="0,66 380,8 760,66 760,80 0,80" fill="var(--brand-blue)"/>
    <polygon points="0,74 380,16 760,74 760,80 0,80" fill="var(--white)"/>
  </svg>

  <section class="intro">
    <h1>Program Design, Implementation, &amp; Evaluation</h1>
    <p>Mara has launched several programs that take into account best practices, as well as particular institutional cultures, participant demographics, and geographical location. The evaluation data of these programs have demonstrated their impact, and she has secured funding and developed key partnerships for program expansion.</p>
  </section>

  <article class="card card--left">
    <div class="card-photo" role="img" aria-label="Mara with a large cheering student cohort by the lakefront">
      <p class="card-caption">Mara with the City Bound pre-orientation civic engagement program cohort</p>
    </div>
    <span class="quote-mark open">&ldquo;</span>
    <p class="quote">Mara has an uncanny ability to combine social change theory and real-world practice in truly compelling ways. For five years at Lakeview University, I saw first-hand how Mara inspired legions of students, created innovative programs, and transformed relationships with community stakeholders. Best of all, she did it with integrity, smarts, enthusiasm and a warm, infectious spirit.</p>
    <span class="quote-mark close">&rdquo;</span>
    <p class="attribution"><strong>Daniel Reyes,</strong> VP, Chief Content Officer, Lakefront Public Radio</p>
  </article>

  <article class="card card--right">
    <div class="card-photo" role="img" aria-label="Mara introducing a panel discussion in front of a projected slide and seated audience">
      <p class="card-caption">Mara introducing the panel discussion on health access in Chicago</p>
    </div>
    <p class="attribution"><strong>Lena Ortiz</strong> Senior Manager of Community Engagement, Northside Scholars</p>
  </article>

  <div class="pattern-band"></div>
  <svg class="site-footer" width="760" height="205" viewBox="0 0 760 205" aria-hidden="true">
    <polygon points="0,68 380,0 760,68 760,205 0,205" fill="var(--footer-dark)"/>
  </svg>

  <footer class="footer-content">
    <div class="brand"><span class="brand-mark"></span><span class="brand-name">Brightwater<br>Civic<br>Advisors</span></div>
    <div class="footer-divider"></div>
    <p class="footer-menu-title">MENU</p>
    <nav class="footer-links">
      <a href="#">About</a><span>|</span>
      <a href="#">Services &amp; Testimonials</a><span>|</span>
      <a href="#">Media &amp; Impact</a><span>|</span>
      <a href="#">Contact</a>
    </nav>
    <p class="copyright">Copyrights @ 2019 All Rights Reserved</p>
  </footer>
</body>
</html>
```